Business card por a urban DJ, up scale audience target

Need a sober design, modern, conservative colors but i can consider some options, y play rnb, hip hop, EDM and top40.

Business card for contact and personal info, double sided, use logo attrached please; im 42 so i need a card acording to my age an target audience.

Target Market(s)

Adult people, up scale audience

Industry/Entity Type

Music Download

Contact Information for Business Card

Cel (318) 4207265518 www.lumadrift.com

Requirements
Must have
• open mind
Nice to have
• open mind
Should not have
• DJ

```html
<!DOCTYPE html>
<html lang="en">
<head>
<meta charset="UTF-8">
<title>LUMA – Business Card</title>
<link href="https://fonts.googleapis.com/css2?family=Roboto:wght@400;500;700;900&display=swap" rel="stylesheet">
<style>
  :root {
    --stage: #e6e4e1;
    --card-light: #f3f3f3;
    --card-dark-top: #3d3d3d;
    --card-dark-bottom: #222222;
    --ink-dark: #2e2e2e;
    --ink-light: #ffffff;
    --ink-muted: #d9d9d9;
    --rule-dark: #3a3a3a;
    --rule-light: #e8e8e8;
  }
  * { box-sizing: border-box; margin: 0; padding: 0; }
  html, body { width: 1200px; height: 902px; overflow: hidden; }
  body {
    background: var(--stage);
    font-family: "Roboto", Arial, sans-serif;
    position: relative;
  }
  .card {
    position: absolute;
    width: 620px;
    height: 354px;
    border-radius: 4px;
    box-shadow: 0 10px 28px rgba(0,0,0,0.22);
    overflow: hidden;
  }
  /* Front side */
  .card-front {
    left: 80px; top: 60px;
    background: var(--card-light);
  }
  .front-brand {
    position: absolute;
    left: 0; right: 0; top: 100px;
    display: flex; align-items: center; justify-content: center; gap: 18px;
    color: var(--ink-dark);
  }
  .brand-square {
    width: 26px; height: 26px;
    background: currentColor;
  }
  .brand-name {
    font-weight: 900;
    font-size: 104px;
    letter-spacing: 4px;
    line-height: 1;
  }
  .front-web {
    position: absolute;
    left: 60px; right: 60px; bottom: 58px;
    display: flex; align-items: center; gap: 16px;
    color: var(--ink-dark);
    font-size: 22px;
  }
  .front-web .rule {
    flex: 1; height: 2px; background: var(--rule-dark);
  }
  /* Back side */
  .card-back {
    left: 500px; top: 478px;
    background: linear-gradient(160deg, var(--card-dark-top), var(--card-dark-bottom));
    color: var(--ink-light);
  }
  .back-brand {
    position: absolute;
    left: 44px; top: 62px;
    display: flex; align-items: center; gap: 14px;
  }
  .back-brand .brand-name { font-size: 88px; }
  .back-brand .brand-square { width: 22px; height: 22px; }
  .back-rule {
    position: absolute;
    left: 0; right: 0; top: 178px;
    height: 2px; background: var(--rule-light);
  }
  .holder {
    position: absolute;
    right: 40px; top: 112px;
    text-align: left;
    background: transparent;
  }
  .holder-name { font-size: 30px; font-weight: 700; }
  .holder-title { font-size: 20px; color: var(--ink-muted); margin-top: 2px; }
  .contact-list {
    position: absolute;
    left: 44px; top: 204px;
    list-style: none;
    font-size: 19px;
  }
  .contact-list li {
    display: flex; align-items: center; gap: 12px;
    margin-bottom: 8px;
  }
  .icon {
    width: 18px; height: 18px;
    background: var(--ink-light);
    border-radius: 2px;
    display: flex; align-items: center; justify-content: center;
    flex: none;
  }
  .icon svg { width: 12px; height: 12px; }
</style>
</head>
<body>

<section class="card card-front">
  <div class="front-brand">
    <span class="brand-square"></span>
    <span class="brand-name">LUMA</span>
  </div>
  <div class="front-web">
    <span class="rule"></span>
    <span>www.lumadrift.com</span>
    <span class="rule"></span>
  </div>
</section>

<section class="card card-back">
  <div class="back-brand">
    <span class="brand-square"></span>
    <span class="brand-name">LUMA</span>
  </div>
  <div class="back-rule"></div>
  <div class="holder">
    <div class="holder-name">Dorian Vale</div>
    <div class="holder-title">Managing Director</div>
  </div>
  <ul class="contact-list">
    <li>
      <span class="icon"><svg viewBox="0 0 12 12"><path d="M2.5 1h2l1 3-1.3 1a6 6 0 0 0 2.8 2.8L8 6.5l3 1v2A1.5 1.5 0 0 1 9.5 11 8.5 8.5 0 0 1 1 2.5 1.5 1.5 0 0 1 2.5 1z" fill="#2e2e2e"/></svg></span>
      (318) 4207265518
    </li>
    <li>
      <span class="icon"><svg viewBox="0 0 12 12"><rect x="1" y="2.5" width="10" height="7" fill="none" stroke="#2e2e2e" stroke-width="1.3"/><path d="M1 2.5l5 4 5-4" fill="none" stroke="#2e2e2e" stroke-width="1.3"/></svg></span>
      info@lumadrift.com
    </li>
    <li>
      <span class="icon"><svg viewBox="0 0 12 12"><circle cx="6" cy="6" r="4.6" fill="none" stroke="#2e2e2e" stroke-width="1.2"/><ellipse cx="6" cy="6" rx="2" ry="4.6" fill="none" stroke="#2e2e2e" stroke-width="1"/><path d="M1.4 6h9.2" stroke="#2e2e2e" stroke-width="1"/></svg></span>
      www.lumadrift.com
    </li>
    <li>
      <span class="icon"><svg viewBox="0 0 12 12"><path d="M6 11S2.5 7 2.5 4.6a3.5 3.5 0 0 1 7 0C9.5 7 6 11 6 11z" fill="#2e2e2e"/><circle cx="6" cy="4.6" r="1.2" fill="#fff"/></svg></span>
      450 Harlow Ave Suite 12, Brookfield, GA 30412
    </li>
  </ul>
</section>

</body>
</html>
```